Christian Media Company Website

I am looking to design an easy to follow, sleek, creative website for my Christian video Bible study platform. On this platform you will be able to sign up to have access to dozens of free high-quality video Bible studies. With that being said There will be a total of 3 pages needed.

First, I will need the home page. This should contain all critical information to inform the customer. The design should be easy to follow, professional, and creative. I will post to some websites I like, if you just copy the website in your design will be removed immediately.

Secondly, we will need a landing Bible study page for people to look through the Bible studies to select one. I have uploaded Study images below with the aspect ratio I want for the design (for each Bible study image). There should be 2 sections Topical studies and Doctrinal Studies (with series under each section). I would like for people to be able to slide left or right through the studies under each category.

Lastly, we will need a video series page. This page needs to have the video they are watching, a playlist of the other videos, as well as a place to put the speaker's image and description. We will have studies that they can download so please make a place for this.

I will upload our color in the files along with our logo! Looking forward to seeing what you all will come up with!

Websites I like :
https://lanternvale.org/
https://www.quillharborfilms.org/
https://www.dunmorel.com/
https://tessavint.org/

Target Market(s)

Christians

Industry/Entity Type

Christian Video Design

Coding

Coded - Design and coding required

Number of Pages Required

3 page

Font styles to use
Sans Serif

Colors
00AB8E
00BBA5
67D7C9
C6EFE9
E9F9F6

Requirements
Should not have
• Pre-Used Templates

```html
<!DOCTYPE html>
<html lang="en">
<head>
<meta charset="utf-8">
<title>Gathered Path – Christian Bible Study Platform</title>
<link href="https://fonts.googleapis.com/css2?family=Open+Sans:wght@400;600;700;800&display=swap" rel="stylesheet">
<style>
  :root{
    --teal-deep:#00AB8E;
    --teal:#00BBA5;
    --teal-soft:#67D7C9;
    --teal-pale:#C6EFE9;
    --teal-mist:#E9F9F6;
    --ink:#1d1d1d;
    --grey-text:#555;
    --field:#f1f1f1;
    --night:#050707;
    --white:#fff;
  }
  *{box-sizing:border-box;margin:0;padding:0}
  html,body{width:1200px;height:3540px;overflow:hidden}
  body{font-family:"Open Sans",Arial,sans-serif;color:var(--ink);background:var(--white);position:relative}
  a{color:inherit;text-decoration:none}

  /* Header / hero */
  .hero{position:absolute;top:0;left:0;width:1200px;height:600px;overflow:hidden}
  .hero-photo{position:absolute;inset:0;background:
      linear-gradient(180deg,rgba(20,22,24,.55),rgba(20,22,24,.35) 60%,rgba(20,22,24,.45)),
      radial-gradient(ellipse at 30% 70%,#c8a57a 0,#6e5236 35%,#2b2522 70%),
      #2b2522}
  .site-nav{position:absolute;top:16px;left:110px;right:110px;height:40px;display:flex;align-items:center}
  .brand{display:flex;align-items:center;gap:10px;color:var(--white);font-weight:700;font-size:16px;letter-spacing:.5px;line-height:1.05;text-transform:uppercase}
  .brand-dot{width:30px;height:30px;border-radius:50%;background:var(--teal)}
  .nav-links{display:flex;gap:40px;margin-left:auto;margin-right:44px;font-size:14px;color:var(--white)}
  .nav-links .active{color:var(--teal-soft)}
  .btn{display:inline-flex;align-items:center;justify-content:center;border-radius:22px;font-weight:600;font-size:14px}
  .btn-teal{background:var(--teal);color:var(--white)}
  .btn-signup{width:120px;height:36px}
  .hero-copy{position:absolute;top:200px;left:0;width:1200px;text-align:center;color:var(--white)}
  .hero-copy h1{font-size:46px;font-weight:700;line-height:1.2}
  .hero-copy p{width:500px;margin:18px auto 0;font-size:15px;line-height:1.5}
  .btn-watch{margin-top:26px;height:42px;padding:0 8px 0 24px;gap:12px}
  .play-dot{width:28px;height:28px;border-radius:50%;background:var(--white);display:flex;align-items:center;justify-content:center}
  .hero-wave{position:absolute;left:0;bottom:0}

  /* Series */
  .series{position:absolute;top:740px;left:0;width:1200px}
  .section-title{font-size:32px;font-weight:600;text-align:center}
  .series-grid{position:absolute;top:122px;left:110px;width:980px;display:grid;grid-template-columns:repeat(3,320px);grid-auto-rows:255px;gap:10px}
  .tile{position:relative;overflow:hidden}
  .tile .fill{position:absolute;inset:0}
  .tile .shade{position:absolute;inset:0;background:linear-gradient(135deg,transparent 45%,rgba(0,187,165,.55) 45%)}
  .study-card{background:var(--teal);color:var(--white);padding:22px 22px}
  .study-card h3{font-size:24px;font-weight:700}
  .study-card p{font-size:13px;line-height:1.45;margin-top:8px;width:230px}
  .speaker{position:absolute;left:22px;bottom:26px;font-size:16px;font-weight:700;display:flex;align-items:center;gap:10px}
  .speaker span.play{width:30px;height:30px;border-radius:50%;background:var(--white);display:flex;align-items:center;justify-content:center}

  /* About */
  .about{position:absolute;top:1740px;left:0;width:1200px;height:485px;overflow:hidden}
  .about-photo{position:absolute;right:0;top:0;width:640px;height:485px;background:linear-gradient(90deg,#0a4b43,#3b4a44 40%,#1b201f)}
  .about-band{position:absolute;inset:0;background:linear-gradient(90deg,var(--teal-deep) 0,var(--teal) 45%,rgba(0,171,142,.15) 70%,transparent 85%)}
  .about-copy{position:absolute;left:110px;top:80px;width:440px;color:var(--white)}
  .about-copy h2{font-size:32px;font-weight:600}
  .about-copy p{font-size:13px;line-height:1.6;margin-top:18px}
  .btn-light{background:var(--white);color:var(--teal-deep);width:136px;height:42px;margin-top:26px}

  /* Contact */
  .contact{position:absolute;top:2225px;left:0;width:1200px;height:520px}
  .contact-info{position:absolute;left:160px;top:76px;width:300px}
  .contact-info h2{font-size:32px;font-weight:600}
  .info-item{display:flex;gap:12px;margin-top:26px}
  .info-item svg{flex:none;margin-top:2px}
  .info-item h4{font-size:14px;font-weight:700}
  .info-item p{font-size:14px;color:var(--grey-text);line-height:1.5}
  .contact-form{position:absolute;left:540px;top:76px;width:280px}
  .field{display:block;width:280px;height:50px;background:var(--field);margin-bottom:14px;font-size:13px;color:#8a8a8a;padding:16px 12px}
  .field.tall{height:64px}
  .btn-submit{width:150px;height:46px;margin-top:6px}

  /* Call to action */
  .cta{position:absolute;top:2745px;left:0;width:1200px;height:300px;overflow:hidden}
  .cta-photo{position:absolute;inset:0;background:linear-gradient(180deg,rgba(0,187,165,.88),rgba(0,171,142,.92)),linear-gradient(90deg,#5a6e64,#8aa092,#4b5a52)}
  .cta-copy{position:absolute;top:55px;width:1200px;text-align:center;color:var(--white)}
  .cta-copy h2{font-size:32px;font-weight:600}
  .cta-copy p{width:640px;margin:10px auto 0;font-size:13px;line-height:1.5}
  .cta-buttons{margin-top:26px;display:flex;justify-content:center;gap:22px}
  .btn-white{background:var(--white);color:var(--teal-deep);width:150px;height:42px}
  .btn-outline{border:2px solid var(--white);color:var(--white);width:130px;height:42px}

  /* Footer */
  .site-footer{position:absolute;top:2950px;left:0;width:1200px;height:590px;color:var(--white)}
  .footer-wave{position:absolute;top:0;left:0}
  .footer-body{position:absolute;top:90px;left:0;width:1200px;height:500px;background:var(--night)}
  .footer-cols{position:absolute;top:110px;left:110px;width:980px;display:flex}
  .footer-brand{width:320px}
  .footer-brand .brand{font-size:22px;color:var(--teal)}
  .footer-brand .brand-dot{width:44px;height:44px}
  .footer-brand p{font-size:14px;line-height:1.5;margin-top:20px;width:240px}
  .footer-col{width:190px}
  .footer-col h4{font-size:18px;font-weight:600;margin-bottom:16px}
  .footer-col li{list-style:none;font-size:13px;margin-bottom:9px;display:flex;align-items:center;gap:8px}
  .footer-col li::before{content:"";width:8px;height:8px;background:var(--teal)}
  .newsletter{width:280px}
  .news-field{width:250px;height:36px;border:1px solid #888;font-size:12px;color:#aaa;padding:9px 10px;position:relative}
  .news-field svg{position:absolute;right:8px;top:10px}
  .socials{display:flex;gap:10px;margin-top:20px}
  .socials span{width:18px;height:18px;border-radius:50%;background:var(--white)}
  .copyright{position:absolute;bottom:0;left:0;width:1200px;height:70px;border-top:1px solid #2a2a2a;font-size:13px;display:flex;align-items:center;justify-content:center}
</style>
</head>
<body>

<header class="hero">
  <div class="hero-photo" role="img" aria-label="Open Bible on a wooden desk beside a laptop, clock and small cross"></div>
  <nav class="site-nav">
    <a class="brand" href="#"><span class="brand-dot"></span>Gathered<br>Path</a>
    <div class="nav-links">
      <a class="active" href="#">Home</a><a href="#">About</a><a href="#">Bible Studies</a><a href="#">Blog</a><a href="#">Contact</a>
    </div>
    <a class="btn btn-teal btn-signup" href="#">Sign Up</a>
  </nav>
  <div class="hero-copy">
    <h1>Christian Bible Study<br>Platform</h1>
    <p>Free video Bible studies for every season of faith. Watch, learn and grow together with your church family and friends.</p>
    <a class="btn btn-teal btn-watch" href="#">Watch Full Video <span class="play-dot"><svg width="10" height="12" viewBox="0 0 10 12"><path d="M0 0L10 6L0 12Z" fill="#00BBA5"/></svg></span></a>
  </div>
  <svg class="hero-wave" width="1200" height="200" viewBox="0 0 1200 200">
    <path d="M0 120 C300 210 700 210 1200 60 L1200 200 L0 200Z" fill="#00BBA5"/>
    <path d="M0 140 C320 215 760 200 1200 110 L1200 200 L0 200Z" fill="#fff"/>
  </svg>
</header>

<section class="series">
  <h2 class="section-title">Our Series</h2>
  <div class="series-grid">
    <div class="tile"><div class="fill" role="img" aria-label="Three crosses on a hill at sunset" style="background:linear-gradient(180deg,#2a2f6a,#b06a6a 55%,#2a1d20)"></div><div class="shade"></div></div>
    <div class="tile"><div class="fill" role="img" aria-label="Black and white series artwork with a hooded figure" style="background:linear-gradient(160deg,#cfcfcf,#6b6b6b 60%,#2d2d2d)"></div><div class="shade"></div></div>
    <div class="tile"><div class="fill" role="img" aria-label="Open Bible held in hands" style="background:linear-gradient(150deg,#9d9a95,#5a5753)"></div><div class="shade"></div></div>

    <div class="tile"><div class="fill" role="img" aria-label="Young woman in a dark t-shirt with series artwork" style="background:linear-gradient(180deg,#0e6e5e,#2b2b2b)"></div><div class="shade"></div></div>
    <div class="tile study-card">
      <h3>Bible Studies</h3>
      <p>Short video lessons that walk through Scripture step by step, ready for groups or personal time.</p>
      <div class="speaker">Micah Danner <span class="play"><svg width="10" height="12" viewBox="0 0 10 12"><path d="M0 0L10 6L0 12Z" fill="#00BBA5"/></svg></span></div>
    </div>
    <div class="tile"><div class="fill" role="img" aria-label="Speaker in a red shirt with revival series artwork" style="background:linear-gradient(160deg,#5f8f6a,#b8544a 60%,#e9e9e9)"></div><div class="shade"></div></div>

    <div class="tile"><div class="fill" role="img" aria-label="Person reading an open Bible" style="background:linear-gradient(150deg,#efeae0,#b9ab93)"></div><div class="shade"></div></div>
    <div class="tile"><div class="fill" role="img" aria-label="Child outdoors in warm light" style="background:linear-gradient(160deg,#c98a3d,#5b4a2e)"></div><div class="shade"></div></div>
    <div class="tile"><div class="fill" role="img" aria-label="Series artwork with a starry sky" style="background:linear-gradient(160deg,#1a3a44,#0b1517)"></div><div class="shade"></div></div>
  </div>
</section>

<section class="about">
  <div class="about-photo" role="img" aria-label="Hands holding a white coffee cup over an open book"></div>
  <div class="about-band"></div>
  <div class="about-copy">
    <h2>About Gathered Path</h2>
    <p>Gathered Path is a home for free, high quality video Bible studies. Our teachers walk through books, themes and doctrines of the faith in clear and simple lessons. Each series comes with notes and questions you can download for your small group, your family or your own quiet time. We believe that every believer can dig deeper into the Word, and we want to make that journey easy, warm and open to all who seek it.</p>
    <a class="btn btn-light" href="#">Learn More</a>
  </div>
</section>

<section class="contact">
  <div class="contact-info">
    <h2>Contact Us</h2>
    <div class="info-item">
      <svg width="14" height="18" viewBox="0 0 14 18"><path d="M7 0C3 0 0 3 0 7c0 5 7 11 7 11s7-6 7-11c0-4-3-7-7-7zm0 9.5A2.5 2.5 0 1 1 7 4.5a2.5 2.5 0 0 1 0 5z" fill="#00BBA5"/></svg>
      <div><h4>Address</h4><p>212 Meadow Lane, Suite 4<br>Brookfield Valley</p></div>
    </div>
    <div class="info-item">
      <svg width="16" height="16" viewBox="0 0 16 16"><path d="M3 0l3 4-2 2c1 2 4 5 6 6l2-2 4 3-2 3C7 16 0 9 0 3z" fill="#00BBA5"/></svg>
      <div><h4>Phone</h4><p>+ 555-010-0000</p></div>
    </div>
    <div class="info-item">
      <svg width="16" height="12" viewBox="0 0 16 12"><rect width="16" height="12" rx="1" fill="#00BBA5"/><path d="M0 1l8 6 8-6" stroke="#fff" fill="none"/></svg>
      <div><h4>Email</h4><p>info@gatheredpath.org</p></div>
    </div>
  </div>
  <form class="contact-form">
    <span class="field">Name</span>
    <span class="field">Phone</span>
    <span class="field">Email</span>
    <span class="field tall">Messages</span>
    <span class="btn btn-teal btn-submit">Submit</span>
  </form>
</section>

<section class="cta">
  <div class="cta-photo" role="img" aria-label="Small group studying the Bible together around a table"></div>
  <div class="cta-copy">
    <h2>Bible Studies</h2>
    <p>Browse topical and doctrinal series, pick a study that fits your group, and download the guides to follow along week by week.</p>
    <div class="cta-buttons">
      <a class="btn btn-white" href="#">Topical studies</a>
      <a class="btn btn-outline" href="#">Download</a>
    </div>
  </div>
</section>

<footer class="site-footer">
  <svg class="footer-wave" width="1200" height="100" viewBox="0 0 1200 100">
    <path d="M0 40 C350 110 800 110 1200 20 L1200 100 L0 100Z" fill="#050707"/>
  </svg>
  <div class="footer-body">
    <div class="footer-cols">
      <div class="footer-brand">
        <a class="brand" href="#"><span class="brand-dot"></span>Gathered<br>Path</a>
        <p>Free video Bible studies to help you know the Word and grow in faith every day.</p>
      </div>
      <div class="footer-col"><h4>Quick Link</h4>
        <ul><li>Home</li><li>About</li><li>Bible Studies</li><li>Blog</li><li>Contact</li></ul></div>
      <div class="footer-col"><h4>Help Link</h4>
        <ul><li>Terms&amp;conditions</li><li>Privacy Policy</li><li>About Us</li><li>Support</li></ul></div>
      <div class="newsletter footer-col"><h4>Get Our Newsletter</h4>
        <div class="news-field">Enter Your Email<svg width="14" height="14" viewBox="0 0 14 14"><path d="M0 7L14 0L10 14L7 8Z" fill="#00BBA5"/></svg></div>
        <div class="socials"><span></span><span></span><span></span><span></span></div>
      </div>
    </div>
    <div class="copyright">@Copyrights 2022 Gathered Path &nbsp;|&nbsp; All Rights Reserved</div>
  </div>
</footer>

</body>
</html>
```